Signs and Symptoms of anemia - poster or flyer

Looking for 2 sections:
first section will have "cartoon" or drawings of the following symptoms: fatique, headache, feeling cold, weakness, dizziness, pica (strange cravings), hairloss, tingling sensation in feet/legs, shortness of breath, brittle nails, irregular heartrate, syncope (fainting), chest pain
second section will have alot (at least 5 of each section below) of pictures with many different ethnics/cultures of thinning hair, cracked/brittle fingernails,
paleness to hands, paleness to nailbeds, paleness to tongue, paleness to conjunctivae   - thinking that for the paleness areas, could also look at normal vs pale

Target Market(s)
those with limited reading comprehension so need alot of pictures depicting the message.
Requirements
Must have
- many pictures with a variety of different ethnicities and cultures displayed

Nice to have
- profession appearance, the pictures represent many different cultures and ethnicities

Should not have
- many words

```html
<!DOCTYPE html>
<html lang="en">
<head>
<meta charset="utf-8">
<title>Signs and Symptoms of Anemia</title>
<link href="https://fonts.googleapis.com/css2?family=Anton&family=Poppins:wght@500;600;700;800&display=swap" rel="stylesheet">
<style>
  :root{
    --maroon:#7a231d;
    --maroon-dark:#5e1a15;
    --teal:#0f968a;
    --teal-dark:#0a7a71;
    --label:#6b6b6b;
    --rule:#d2d2d2;
    --icon-fill:#dcdcdc;
    --icon-core:#e8e8e8;
    --stage:#ececec;
  }
  *{box-sizing:border-box;margin:0;padding:0}
  html,body{width:1200px;height:1200px;overflow:hidden;background:var(--stage)}
  .flyer{
    position:absolute;left:153px;top:20px;width:1209px;height:1567px;
    transform:scale(0.74);transform-origin:0 0;
    background:linear-gradient(90deg,#f4f4f4,#ffffff 50%,#f4f4f4);
    font-family:'Poppins',sans-serif;overflow:hidden;
  }
  .title-band{position:absolute;left:0;top:0;width:100%;height:125px}
  .title-lead{
    position:absolute;left:42px;top:22px;font-family:'Anton',sans-serif;font-weight:400;
    font-size:70px;color:#fff;letter-spacing:0.5px;line-height:1;white-space:nowrap;
  }
  .title-key{
    position:absolute;left:848px;top:20px;font-family:'Anton',sans-serif;font-weight:400;
    font-size:108px;color:var(--teal);line-height:1;letter-spacing:-1px;
  }
  .symptom{position:absolute;width:180px;margin-left:-90px;text-align:center}
  .symptom svg{display:block;margin:0 auto}
  .symptom-label{
    margin-top:12px;font-size:20px;font-weight:600;color:var(--label);line-height:1.3;
  }
  .rule{position:absolute;left:43px;width:1123px;height:2px;background:var(--rule)}
  .culture-panel{
    position:absolute;left:0;top:890px;width:100%;height:667px;
    background:radial-gradient(ellipse at 50% 60%,#0aa293,var(--teal-dark) 80%);
  }
  .bottom-rule{position:absolute;left:0;bottom:0;width:100%;height:10px;background:var(--maroon)}
  .culture-tab{position:absolute;left:250px;top:0;width:710px;height:75px}
  .culture-title{
    position:absolute;left:250px;top:10px;width:710px;text-align:center;
    font-family:'Anton',sans-serif;font-weight:400;font-size:48px;color:#fff;line-height:1.1;
  }
  .photo-card{
    position:absolute;top:102px;width:438px;height:255px;background:#fff;
    border-radius:22px;padding:8px;
  }
  .photo-card .photo{height:195px;border-radius:16px}
  .photo-caption{
    text-align:center;margin-top:14px;font-size:21px;font-weight:700;color:var(--maroon);
  }
  .hair-photo{background:linear-gradient(120deg,#6b6056,#c7aa98 45%,#5a6e5a)}
  .nail-photo{background:linear-gradient(120deg,#2fa796,#6b3b26 45%,#2d9b8b)}
  .panel-rule{position:absolute;left:43px;top:385px;width:1123px;height:1px;background:rgba(255,255,255,0.15)}
  .round-photo{
    position:absolute;top:418px;width:208px;height:208px;border-radius:50%;
    border:6px solid #fff;
  }
  .tongue-before{background:radial-gradient(circle at 50% 60%,#e88c88,#e0b49c 55%,#d9a78f)}
  .tongue-after{background:radial-gradient(circle at 50% 60%,#f1bdb2,#e6bfa8 55%,#dcae96)}
  .hand-before{background:linear-gradient(135deg,#8b5d43,#c9957a 55%,#7fae86)}
  .hand-after{background:linear-gradient(135deg,#1e2a33,#d9c98f 50%,#aec6d8)}
  .state-tag{
    position:absolute;top:522px;font-weight:800;font-size:44px;color:#fff;
    transform:translate(-50%,-50%) rotate(-90deg);letter-spacing:1px;
  }
  .step-arrow{position:absolute;left:578px;top:508px}
</style>
</head>
<body>
<svg width="0" height="0" style="position:absolute">
  <defs>
    <symbol id="ring" viewBox="0 0 110 110">
      <circle cx="55" cy="55" r="43" fill="#dcdcdc"/>
      <circle cx="55" cy="55" r="32" fill="#e8e8e8"/>
      <path d="M51 5 A50 50 0 0 0 51 105" fill="none" stroke="#7a231d" stroke-width="5"/>
      <path d="M59 5 A50 50 0 0 1 59 105" fill="none" stroke="#0f968a" stroke-width="5"/>
    </symbol>
  </defs>
</svg>

<main class="flyer">
  <svg class="title-band" viewBox="0 0 1209 125" preserveAspectRatio="none">
    <path d="M0 0 H840 L790 100 Q778 125 750 125 H0 Z" fill="#7a231d"/>
    <rect x="0" y="0" width="1209" height="8" fill="#7a231d"/>
  </svg>
  <h1 class="title-lead">SIGNS AND SYMPTOMS OF</h1>
  <div class="title-key">ANEMIA</div>

  <div class="symptom" style="left:115px;top:183px"><svg width="108" height="108" role="img" aria-label="Line icon of a tired person with swirls (fatigue)"><use href="#ring"/></svg><p class="symptom-label">FATIQUE</p></div>
  <div class="symptom" style="left:310px;top:183px"><svg width="108" height="108" role="img" aria-label="Line icon of a person with a headache"><use href="#ring"/></svg><p class="symptom-label">HEADACHE</p></div>
  <div class="symptom" style="left:505px;top:183px"><svg width="108" height="108" role="img" aria-label="Line icon of a person feeling cold"><use href="#ring"/></svg><p class="symptom-label">FEELING COLD</p></div>
  <div class="symptom" style="left:701px;top:183px"><svg width="108" height="108" role="img" aria-label="Line icon of a sleepy eye (weakness)"><use href="#ring"/></svg><p class="symptom-label">WEAKNESS</p></div>
  <div class="symptom" style="left:897px;top:183px"><svg width="108" height="108" role="img" aria-label="Line icon of a dizzy face with spiral eyes"><use href="#ring"/></svg><p class="symptom-label">DIZZINESS</p></div>
  <div class="symptom" style="left:1093px;top:183px"><svg width="108" height="108" role="img" aria-label="Line icon of a comb (hair loss)"><use href="#ring"/></svg><p class="symptom-label">HAIRLOSS</p></div>

  <div class="rule" style="top:365px"></div>

  <div class="symptom" style="left:307px;top:394px"><svg width="108" height="108" role="img" aria-label="Line icon of a fingertip nail (brittle nails)"><use href="#ring"/></svg><p class="symptom-label">BRITTLE NAILS</p></div>
  <div class="symptom" style="left:503px;top:394px"><svg width="108" height="108" role="img" aria-label="Line icon of a hand on the chest (chest pain)"><use href="#ring"/></svg><p class="symptom-label">CHEST PAIN</p></div>
  <div class="symptom" style="left:699px;top:394px"><svg width="108" height="108" role="img" aria-label="Line icon of a person short of breath"><use href="#ring"/></svg><p class="symptom-label">SHORTNESS<br>OF BREATH</p></div>
  <div class="symptom" style="left:893px;top:394px"><svg width="108" height="108" role="img" aria-label="Line icon of a heart with a pulse line"><use href="#ring"/></svg><p class="symptom-label">IRREGULAR<br>HEARTRATE</p></div>

  <div class="rule" style="top:595px"></div>

  <div class="symptom" style="left:407px;top:631px"><svg width="108" height="108" role="img" aria-label="Line icon of a fainting person"><use href="#ring"/></svg><p class="symptom-label">SYNCOPE<br>(FAINTING)</p></div>
  <div class="symptom" style="left:603px;top:631px"><svg width="108" height="108" role="img" aria-label="Line icon of a thought bubble (strange cravings)"><use href="#ring"/></svg><p class="symptom-label">PICA (STRANGE<br>CRAVINGS)</p></div>
  <div class="symptom" style="left:799px;top:631px"><svg width="108" height="108" role="img" aria-label="Line icon of a tingling leg muscle"><use href="#ring"/></svg><p class="symptom-label">TINGLING<br>SENSATION<br>IN FEET/LEGS</p></div>

  <section class="culture-panel">
    <svg class="culture-tab" viewBox="0 0 710 75" preserveAspectRatio="none">
      <path d="M0 0 H710 L682 55 Q672 75 648 75 H62 Q38 75 28 55 Z" fill="#7a231d"/>
    </svg>
    <h2 class="culture-title">DIFFERENT ETHNICS/CULTURES</h2>

    <figure class="photo-card" style="left:137px">
      <div class="photo hair-photo" role="img" aria-label="Photo of a scalp with thinning hair"></div>
      <figcaption class="photo-caption">THINNING HAIR</figcaption>
    </figure>
    <figure class="photo-card" style="left:632px">
      <div class="photo nail-photo" role="img" aria-label="Photo of fingers with cracked brittle fingernails"></div>
      <figcaption class="photo-caption">CRACKED/BRITTLE FINGERNAILS</figcaption>
    </figure>

    <div class="panel-rule"></div>

    <div class="round-photo tongue-before" style="left:66px" role="img" aria-label="Photo of a tongue before treatment"></div>
    <span class="state-tag" style="left:312px">BEFORE</span>
    <div class="round-photo hand-before" style="left:353px" role="img" aria-label="Photo of a hand before treatment"></div>
    <svg class="step-arrow" width="30" height="30" viewBox="0 0 30 30"><path d="M0 0 L30 15 L0 30 Z" fill="#7a231d"/></svg>
    <div class="round-photo tongue-after" style="left:649px" role="img" aria-label="Photo of a pale tongue after"></div>
    <span class="state-tag" style="left:895px">AFTER</span>
    <div class="round-photo hand-after" style="left:935px" role="img" aria-label="Photo of a pale palm after"></div>

    <div class="bottom-rule"></div>
  </section>
</main>
</body>
</html>
```